TRELOS - Web Design Project

Task Description
RELOS is the major GLOVRA project supporting the Indonesian Bureau of Tidal Works and Harvests (BTWH). BTWH is responsible for promoting sustainable use of fish and other marine resources for Indonesia’s long-term economic prosperity. Its mandate encompasses such issues as drafting of marine and fisheries sector policies; control of overfishing, destructive and illegal fishing practices; spatial planning for resource use; management of conservation areas; data analysis and modeling for fisheries management; and promoting the long-term welfare of fishing communities. The TRELOS project is supporting BTWH efforts to achieve sustainability in the marine and fisheries sector and to improve the response of coastal communities to near-term disasters and long-term impacts related to climate change.

The TRELOS project has three key thematic areas: [policy] [1], [sustainable fisheries] [2], and [climate change] [3] — as well as supporting overall coordination of [Coastal Stewardship Scheme] [4] activities.
Updates

Project Deadline Extended
Reason: There are two public holidays in Indonesia so we are unable to provide feedback to designers between 17th and the 20th.

a few people have asked for reference sites - there is really no reference site we can give but I have attached a jpg for some ideas - we are after innovated ideas that will capture people's attention but which is extermely easy to use and navigate. 

the main focus should be on a map on Indonesia with focal points of our three offices (and with great navigation buttons/tools). 

please give us something amazing and use your design skills to make an amazing site

thanks

Target Market(s)

under 25, college or uni - research students - others interested in marine and fisheries

Industry/Entity Type

Sustainability

Requirements
Must have
• The web must have Indonesia map on the center with button on Jakarta city as headquarter, Sulawesi Tenggara (Wakatobi) as branch office and Nusa Tenggara Barat (Mataram), must have an icon for navigation on the upper, left or bottom side. Example of layout is attached (only as example). The "buttons" should then be used as navigation tools

We are after innovative ideas that with easy navigation features.

Current website is www.trelosworks.com - this is seen as too hard to navigate

Navigation Icons will also need to be developed;
- About
- Activities
- News
Library
Press releases
Publications
- Partners
- Links

site will also need to adhere to these the GLOVRA branding guidelines
http://www.glovra.example/identity/GLOVRA_Visual_Rules_Guide.pdf

TRELOS Logo is attached

Nice to have
• - based on scaffold plinko, site will be hosted on stavelo9 platform. (http://plinko.codebarn.example/)

```html
<!DOCTYPE html>
<html lang="en">
<head>
<meta charset="utf-8">
<title>TRELOS – Coastal Marine Resilience Support</title>
<link rel="stylesheet" href="https://fonts.googleapis.com/css2?family=Arimo:wght@400;700&display=swap">
<style>
:root{
  --blue:#1b5fa8;
  --navy:#0e3f86;
  --red:#c8102e;
  --text:#666;
  --muted:#999;
  --line:#dde3ea;
  --hero:#2e2e2e;
  --page:#ececec;
  --footer-top:#1f63b4;
  --footer-bottom:#0a3a7c;
}
*{box-sizing:border-box;margin:0;padding:0}
html,body{width:972px;height:1200px;overflow:hidden}
body{background:var(--page);font-family:Arimo,Arial,sans-serif;color:var(--text);font-size:12px;position:relative}
.abs{position:absolute}

.topline{left:0;top:0;width:972px;height:4px;background:var(--red)}
.header{left:0;top:4px;width:972px;height:88px;background:linear-gradient(#fff,#f4f4f4)}
.brand{left:23px;top:12px}
.brand-name{display:flex;align-items:center;gap:8px;font-size:25px;font-weight:700;color:var(--navy);letter-spacing:.3px}
.brand-dot{width:34px;height:34px;border-radius:50%;background:var(--navy)}
.brand-bar{margin-top:6px;width:282px;height:16px;background:var(--navy);color:#fff;font-size:7.5px;font-weight:700;display:flex;align-items:center;justify-content:center}
.contact{right:20px;top:55px;display:flex;align-items:center;gap:10px}
.phone{display:flex;align-items:center;gap:6px;font-size:13px;color:#8a8a8a}
.search{display:flex}
.search span{width:147px;height:26px;border:1px solid #ccc;background:#fff;font-size:11px;color:#bbb;padding:6px 12px}
.search b{width:28px;height:26px;background:var(--blue);display:flex;align-items:center;justify-content:center}

.nav{left:0;top:92px;width:972px;height:35px;background:linear-gradient(#fff,#eef0f2);border-top:1px solid #ddd;border-bottom:1px solid #ddd;display:flex;align-items:center;padding-left:20px;gap:21px}
.nav a{display:flex;align-items:center;gap:7px;font-size:12px;font-weight:700;color:var(--navy);text-decoration:none}
.nav i{width:22px;height:22px;border-radius:5px;background:linear-gradient(#5aa0e8,#1b5fa8);display:block}

.hero{left:0;top:137px;width:972px;height:359px;background:var(--hero)}
.hero-map{left:0;top:0;width:736px;height:359px;background:radial-gradient(ellipse at 50% 55%,#d9d9d9 0%,#8a8a8a 45%,#3a3a3a 80%)}
.pin{display:flex;flex-direction:column;align-items:center}
.pin-label{background:#3d3d3d;color:#fff;font-size:10.5px;font-weight:700;padding:4px 7px;border-radius:2px}
.pin-dot{width:10px;height:10px;border-radius:50%;background:#fff;margin-top:8px}
.pin-dot.hq{background:#1e7ff0}
.hero-panel{left:736px;top:0;width:218px;height:359px;background:rgba(60,60,60,.9);padding:28px 20px 0}
.hero-panel h2{font-size:11.5px;color:#aaa;font-weight:700;margin-bottom:22px}
.hero-panel p{font-size:11px;line-height:19px;color:#777;text-align:justify;margin-bottom:26px}
.hero-panel strong{color:#aaa}
.view-more{position:absolute;right:10px;bottom:12px;font-size:10.5px;font-weight:700;color:#ddd}

.content{left:19px;top:511px;width:935px;height:596px;background:#fff;border:1px solid #ddd;box-shadow:0 0 4px rgba(0,0,0,.1)}
.card{top:528px;width:213px;height:160px;border:1px solid var(--line);background:linear-gradient(#fff 60%,#f3f3f3)}
.card-head{height:38px;background:linear-gradient(#fff,#eaeaea);display:flex;align-items:center;gap:8px;padding-left:8px;font-size:13px;font-weight:700;color:var(--navy);line-height:15px}
.card-icon{width:30px;height:30px;border-radius:50%;flex:none}
.card p{padding:12px 10px 0;font-size:11.5px;line-height:19px;text-align:justify;color:var(--text)}
.more{color:var(--red);font-weight:700}

.section-title{font-size:14px;font-weight:700;color:var(--muted);padding-bottom:10px;border-bottom:1px solid #eee}
.section-title span{color:var(--navy)}
.news{left:36px;top:711px;width:671px}
.news h3{font-size:13px;color:var(--navy);margin:14px 0 6px 2px;letter-spacing:.3px}
.news p{font-size:11.5px;line-height:19px;text-align:justify;word-spacing:2px}
.news .more{font-weight:400}
.news hr{border:0;border-top:1px dashed #ddd;margin:10px 0 0}
.news-item{display:flex;gap:10px}
.news-thumb{width:88px;height:66px;flex:none;border:1px solid #ddd;background:radial-gradient(circle,#5b7fd1,#2a3f8f 60%,#fff 62%)}

.gallery{top:940px}
.gallery-box{margin-top:8px;height:127px;border:2px solid #d8e2ee;display:flex;gap:16px;padding:8px 0 0 16px;position:relative}
.shot{width:147px;height:106px;background:linear-gradient(#6b9ed8,#c9dcee 55%,#4c8bbf 75%,#e8e2cf)}
.shot-cap{display:flex;align-items:flex-end;justify-content:center;padding-bottom:6px;font-size:13px;font-weight:700;color:#0e3f86}
.arrow{position:absolute;top:45px;width:24px;height:24px;border-radius:50%;background:#fff;border:1px solid #ccc;display:flex;align-items:center;justify-content:center}

.side-box{left:724px;width:213px;border:1px solid var(--line);background:#fff}
.side-box h4{height:26px;padding:5px 12px;font-size:14px;font-weight:700;color:var(--red);background:linear-gradient(#fff,#ececec)}
.side-box h4 span{color:var(--navy)}
.signup-body{display:flex;gap:10px;padding:4px 6px 0}
.globe{width:78px;height:56px;flex:none;background:radial-gradient(circle at 40% 40%,#6ec3f2,#1c6bb8 60%,#fff 62%)}
.signup-body p{font-size:11px;line-height:14px;color:#888;text-align:justify}
.signup-form{display:flex;margin:8px 0 0 4px}
.signup-form span{width:145px;height:24px;border:1px solid #ccc;font-size:11px;color:#ccc;padding:5px 8px}
.signup-form b{width:64px;height:24px;background:var(--blue);color:#fff;font-size:11.5px;display:flex;align-items:center;justify-content:center}
.meeting{padding:0 12px}
.meeting div{padding:8px 0 6px;border-bottom:1px dashed #ddd;font-size:11.5px;line-height:17px;color:var(--navy)}
.meeting div:last-of-type{border:0}
.meeting b{display:block;color:var(--blue);font-size:11.5px;margin-bottom:2px}
.meeting-more{text-align:right;font-weight:700;color:var(--blue);font-size:11.5px}

.footer{left:0;top:1113px;width:972px;height:70px;background:linear-gradient(var(--footer-top),var(--footer-bottom));color:#fff;padding:9px 19px;font-size:10.5px;line-height:18px}
.footer-links{position:absolute;right:18px;top:9px;font-size:11.5px}
.footer-links span{margin:0 6px}
.social{position:absolute;right:18px;top:36px;display:flex;gap:6px}
.social i{width:22px;height:22px;border-radius:3px;background:#8fb6e0;display:block}
</style>
</head>
<body>
<div class="abs topline"></div>

<header class="abs header">
  <div class="abs brand">
    <div class="brand-name"><span class="brand-dot"></span>GLOVRA | INDONESIA</div>
    <div class="brand-bar">COASTAL MARINE RESILIENCE SUPPORT (TRELOS) PROJECT</div>
  </div>
  <div class="abs contact">
    <div class="phone">
      <svg width="26" height="24" viewBox="0 0 26 24"><path d="M5 3c-2 1-3 4 0 9s8 9 12 10c2 0 4-1 4-3l-4-4-3 2c-2-1-5-4-6-6l2-3z" fill="#222"/><circle cx="19" cy="7" r="6" fill="none" stroke="#f2a300" stroke-width="2"/></svg>
      +100 555 0142
    </div>
    <div class="search"><span>Search something....</span><b><svg width="13" height="13" viewBox="0 0 13 13"><circle cx="5.5" cy="5.5" r="4" fill="none" stroke="#fff" stroke-width="2"/><path d="M8.5 8.5l3.5 3.5" stroke="#fff" stroke-width="2"/></svg></b></div>
  </div>
</header>

<nav class="abs nav">
  <a href="#"><i></i>ABOUT US</a>
  <a href="#"><i></i>ACTIVITIES</a>
  <a href="#"><i></i>NEWS</a>
  <a href="#"><i></i>LIBRARY</a>
  <a href="#"><i></i>PRESS RELEASE</a>
  <a href="#"><i></i>PUBLICITY</a>
  <a href="#"><i></i>PARTNERS</a>
  <a href="#"><i></i>LINKS</a>
</nav>

<section class="abs hero">
  <div class="abs hero-map" role="img" aria-label="Map of the Indonesian archipelago in white on dark grey"></div>
  <div class="abs pin" style="left:196px;top:267px"><span class="pin-label">JAKARTA</span><span class="pin-dot hq"></span></div>
  <div class="abs pin" style="left:378px;top:211px"><span class="pin-label">SULAWESI</span><span class="pin-dot"></span></div>
  <div class="abs pin" style="left:359px;top:290px"><span class="pin-label">LOMBOK</span><span class="pin-dot"></span></div>
  <div class="abs hero-panel">
    <h2>CONTENT TITLE HERE</h2>
    <p>Lorem ipsum dolor sit ipsumLorem ipsum dolor sit ipsumLorem ipsum dolor sit ipsumLorem ipsum dolor sit ipsumLorem ipsum dolor sit usm L orem ipsum dolor. <strong>More...</strong></p>
    <p>Lorem ipsum dolor sit ipsumLorem ipsum dolor sit ipsumLorem ipsum dolor sit ipsumLorem ipsum dolor sit ipsumLorem ipsum dolor sit usm L orem ipsum dolor. <strong>More...</strong></p>
    <span class="view-more">VIEW MORE...</span>
  </div>
</section>

<main>
  <div class="abs content"></div>

  <article class="abs card" style="left:36px"><div class="card-head"><span class="card-icon" style="background:#1d6fc2"></span>Policy</div><p>Lorem ipsum dolor sit ipsumLorem ipsum dolor sit ipsumLorem ipsum dolor sit ipsumLorem ipsum dolor sit ipsumLorem ipsum dolor sit usm L orem ipsum dolor. <span class="more">More...</span></p></article>
  <article class="abs card" style="left:265px"><div class="card-head"><span class="card-icon" style="background:#7ccb2e"></span>Sustainable Fisheries</div><p>Lorem ipsum dolor sit ipsumLorem ipsum dolor sit ipsumLorem ipsum dolor sit ipsumLorem ipsum dolor sit ipsumLorem ipsum dolor sit usm L orem ipsum dolor. <span class="more">More...</span></p></article>
  <article class="abs card" style="left:494px"><div class="card-head"><span class="card-icon" style="background:linear-gradient(135deg,#2a7bd6,#4cb648)"></span>Climate Changes</div><p>Lorem ipsum dolor sit ipsumLorem ipsum dolor sit ipsumLorem ipsum dolor sit ipsumLorem ipsum dolor sit ipsumLorem ipsum dolor sit usm L orem ipsum dolor. <span class="more">More...</span></p></article>
  <article class="abs card" style="left:724px"><div class="card-head"><span class="card-icon" style="background:#1a5fb4"></span>Coastal Stewardship<br>Scheme</div><p>Lorem ipsum dolor sit ipsumLorem ipsum dolor sit ipsumLorem ipsum dolor sit ipsumLorem ipsum dolor sit ipsumLorem ipsum dolor sit usm L orem ipsum dolor. <span class="more">More...</span></p></article>

  <section class="abs news">
    <div class="section-title">Letest <span>News</span></div>
    <h3>News Title Here</h3>
    <p>Lorem ipsum dolor sit ipsumLorem ipsum dolor sit ipsumLorem ipsum dolor sit ipsumLorem ipsum dolor sit ipsumLoremLorem ipsum dolor sit ipsumLorem <span class="more">More...</span></p>
    <hr>
    <h3>News Title Here</h3>
    <div class="news-item">
      <div class="news-thumb" role="img" aria-label="Globe illustration"></div>
      <p>Lorem ipsum dolor sit ipsumLorem ipsum dolor sit ipsumLorem ipsum dolor sit ipsumLorem ipsum dolor sit ipsumLoremLorem ipsum dolor sit ipsumLorem Lorem ipsum dolor sit ipsumLorem ipsum dolor sit ipsumLorem ipsum dolor sit ipsumLorem ipsum dol or sit jdlkgjdlgjdlk ipsumLorem ipsum dolor sit ipsumLorem <span class="more">More...</span></p>
    </div>
  </section>

  <section class="abs gallery" style="left:36px;width:336px">
    <div class="section-title" style="border:0;padding:0">Letest <span>Photos</span></div>
    <div class="gallery-box">
      <div class="shot shot-cap" role="img" aria-label="Beach with blue sky and clouds">Pantai Biak</div>
      <div class="shot" role="img" aria-label="Sea under a cloudy sky"></div>
      <span class="arrow" style="left:-14px"><svg width="10" height="10" viewBox="0 0 10 10"><path d="M7 1L2 5l5 4z" fill="#0e3f86"/></svg></span>
      <span class="arrow" style="right:-14px"><svg width="10" height="10" viewBox="0 0 10 10"><path d="M3 1l5 4-5 4z" fill="#c8102e"/></svg></span>
    </div>
  </section>
  <section class="abs gallery" style="left:391px;width:315px">
    <div class="section-title" style="border:0;padding:0">Letest <span>videos</span></div>
    <div class="gallery-box" style="padding-left:8px">
      <div class="shot" role="img" aria-label="Video still of a sea and clouds" style="display:flex;align-items:center;justify-content:center"><svg width="26" height="30" viewBox="0 0 26 30"><path d="M24 1L2 15l22 14z" fill="#fff" opacity=".8"/></svg></div>
      <div class="shot" role="img" aria-label="Video still of a sea and clouds" style="display:flex;align-items:center;justify-content:center"><svg width="26" height="30" viewBox="0 0 26 30"><path d="M24 1L2 15l22 14z" fill="#fff" opacity=".8"/></svg></div>
    </div>
  </section>

  <aside class="abs side-box" style="top:711px;height:114px">
    <h4><span>Signup</span> Newsletter</h4>
    <div class="signup-body"><div class="globe" role="img" aria-label="Globe with newspaper illustration"></div><p>ipsumLorem ipsum dolor sit ipsumLorem ipsum dolor sit</p></div>
    <div class="signup-form"><span>Email here</span><b>SIGN UP</b></div>
  </aside>
  <aside class="abs side-box" style="top:840px;height:252px">
    <h4><span>Meeting</span> Calendar</h4>
    <div class="meeting">
      <div><b>Date : 21-05-2012</b>Lorem ipsum dolor ispLorem ipsum dolor ispLorem ipsum dolor isp</div>
      <div><b>Date : 21-05-2012</b>Lorem ipsum dolor ispLorem ipsum dolor ispLorem ipsum dolor isp</div>
      <div><b>Date : 21-05-2012</b>Lorem ipsum dolor ispLorem ipsum dolor ispLorem ipsum dolor isp</div>
      <p class="meeting-more">More....</p>
    </div>
  </aside>
</main>

<footer class="abs footer">
  <p>Copyright © 2012-2014 Haldrin Partners Inc. TRELOS - Privacy policy</p>
  <p>The information provided on this website is not official Veltaran Government information and does not represent the views</p>
  <p>or positions of the Global Visionary Relief Agency or the Veltaran Government.</p>
  <div class="footer-links">Home<span>|</span>About Us<span>|</span>Our Activities<span>|</span>Contact Us</div>
  <div class="social"><i></i><i></i><i></i></div>
</footer>
</body>
</html>
```